Locksmith SmartPhone Web Design Project

I am a locksmith and focus on customers that use their smart phones to find me. I have a static web page that I created myself but it is horrible. See for yourself at www.brackenlocksmiths.com.au

I want a cross-platform static site that simply shows the information and with the ability to change minor items like pricing. I want it to be compelling in its look and feel (not overwhelming) but simple. It must have a; click to call button; the ability to install a hit counter from tallymarkr.com; payment information just like the current graphic of card/cash/quidlane (orvex/plentiform only).

This will be hosted on my own server.
Updates

Hello Designers,

I have updated the brief in the must have and nice to have fields.

Thank you all,

Trent.

Hello to all Designers,

There is about 9 days left before the deadline. The overall level of competition is extremely high and I would like to thank all the designers who have submitted so far, 27 submissions in total so far. Excellent work.

If you have submitted already and wish to provide new designs, I am keen to see them. 

Hi guys, time is almost up. Please submit any new designs that you may have. The quality has been excellent so far.

Trent.

Target Market(s)

People who are locked out of their house/shop/office etc.

Industry/Entity Type

Locksmith

Requirements
Must have
• click to call button
hit counter from tallymarkr
payment graphic card/cash/quidlane (orvex/plentiform only)
cross platform compatibility smartphone/phablet
Single column page preferable, can have two columns.
Nice to have
• When the page loads regardless of the mobile device, all info should be presented. In other words no vertical or horizontal scroll bars.
Should not have
• hidden code, advertising, credits etc

```html
<!DOCTYPE html>
<html lang="en">
<head>
<meta charset="utf-8">
<title>Bracken Locksmiths</title>
<link href="https://fonts.googleapis.com/css2?family=Roboto+Condensed:wght@400;700&display=swap" rel="stylesheet">
<style>
  :root{
    --canvas:#ffffff;
    --gold:#f5b800;
    --gold-deep:#f0b400;
    --orange:#e8830f;
    --orange-text:#e0880a;
    --charcoal:#1e1e1e;
    --charcoal-2:#3a3a3a;
    --grey-text:#8a8a8a;
    --light-grey:#d6d6d6;
    --rule:#e2e2e2;
    --white:#ffffff;
  }
  *{box-sizing:border-box;margin:0;padding:0}
  html,body{width:1066px;height:1200px;overflow:hidden;background:var(--canvas)}
  body{font-family:"Roboto Condensed",sans-serif;position:relative}
  .page{
    position:absolute;left:191px;top:24px;width:683px;height:1151px;
    background:linear-gradient(90deg,#cfcfcf 0,#f4f4f4 11px,#fff 14px,#fff 669px,#f4f4f4 672px,#cfcfcf 683px);
    overflow:hidden;
  }
  .site-header{
    position:absolute;left:0;top:0;width:100%;height:115px;
    background:linear-gradient(#ffffff,#e3e3e3);
    border-bottom:2px solid #c9c9c9;
    display:flex;align-items:center;justify-content:center;
  }
  .brand{color:var(--gold);font-size:56px;font-weight:400;letter-spacing:0.5px}
  .brand sup{font-size:26px;vertical-align:28px}
  .offer{
    position:absolute;left:11px;top:125px;width:661px;height:95px;
    border:3px solid var(--orange);background:var(--white);
    color:var(--orange-text);font-size:28px;line-height:34px;text-align:center;
    display:flex;flex-direction:column;justify-content:center;
  }
  .section-bar{
    position:absolute;left:11px;top:244px;width:661px;height:70px;
    background:linear-gradient(#111,#2d2d2d);
    color:#bdbdbd;font-size:28px;line-height:70px;padding-left:12px;
  }
  .team-photo{
    position:absolute;left:14px;top:314px;width:655px;height:347px;
    background:linear-gradient(90deg,#d9d9d9,#8e8f93 40%,#5f6066 65%,#c4c4c4);
  }
  .availability{
    position:absolute;left:14px;top:672px;width:655px;height:90px;
    background:linear-gradient(var(--gold),var(--gold-deep));
    display:flex;align-items:center;justify-content:space-between;padding:0 37px 0 28px;
  }
  .availability h2{color:var(--white);font-size:42px;font-weight:400}
  .status-btn{
    width:82px;height:49px;border-radius:5px;background:linear-gradient(#3b3b3b,#111);
    color:var(--white);font-size:28px;line-height:49px;text-align:center;
  }
  .call-bar{
    position:absolute;left:11px;top:773px;width:658px;height:92px;
    background:linear-gradient(#ececec,#c8c8c8);
    border-radius:46px 4px 4px 46px;
    display:flex;align-items:center;
  }
  .call-icon{
    width:109px;height:92px;border-radius:46px 0 0 46px;
    background:linear-gradient(#4a4a4a,#222);display:flex;align-items:center;justify-content:center;
  }
  .call-label{margin-left:42px;font-size:39px;color:var(--grey-text)}
  .call-label a{color:var(--orange-text);text-decoration:none;margin-left:24px}
  .payments{position:absolute;left:0;top:888px;width:100%;display:flex;justify-content:center;gap:8px}
  .pay{
    width:112px;height:72px;display:flex;align-items:center;justify-content:center;
    font-size:20px;font-weight:700;border:2px solid #ddd;background:var(--white);color:#1f3c88;
  }
  .pay.plentiform{color:#c4261d}
  .pay.quidlane{color:#1f3c88;border-color:#f3b36a;background:#fff6e6}
  .pay.cash{border:none;background:linear-gradient(120deg,#9ccfd2,#e28aa0 45%,#f0c24c 75%,#6fa36a)}
  .divider{position:absolute;left:14px;top:983px;width:655px;height:1px;background:var(--rule)}
  .legal{position:absolute;left:0;top:994px;width:100%;text-align:center;color:var(--grey-text);font-size:18px;line-height:28px}
  .site-footer{
    position:absolute;left:0;top:1075px;width:100%;height:76px;
    background:linear-gradient(#2a2a2a,#444);
    color:var(--white);font-size:18px;line-height:76px;text-align:center;
  }
</style>
</head>
<body>
<main class="page">
  <header class="site-header"><h1 class="brand">BRACKEN LOCKSMITHS<sup>®</sup></h1></header>
  <div class="offer"><span>LOCKED OUT?</span><span>$150 GETS YOU IN. EASY!</span></div>
  <div class="section-bar">LOCKSMITH LOCKOUT SERVICE</div>
  <div class="team-photo" role="img" aria-label="Photo of the locksmith team in business suits"></div>
  <div class="availability"><h2>LOCKSMITH AVAILABLE?</h2><span class="status-btn">YES</span></div>
  <div class="call-bar">
    <span class="call-icon">
      <svg width="56" height="56" viewBox="0 0 56 56" aria-hidden="true">
        <circle cx="28" cy="28" r="26" fill="#f5b800" stroke="#111" stroke-width="2"/>
        <rect x="21" y="15" width="15" height="25" rx="3" fill="none" stroke="#111" stroke-width="3" transform="rotate(-20 28 28)"/>
        <path d="M14 22 q-3 6 0 12 M40 22 q3 6 0 12" fill="none" stroke="#111" stroke-width="2.5"/>
      </svg>
    </span>
    <span class="call-label">CLICK TO CALL<a href="tel:0491570156">0491570156</a></span>
  </div>
  <div class="payments">
    <span class="pay plentiform">Plentiform</span>
    <span class="pay orvex">ORVEX</span>
    <span class="pay cash" role="img" aria-label="Cash banknotes"></span>
    <span class="pay quidlane">Quidlane</span>
  </div>
  <div class="divider"></div>
  <p class="legal">ABN: 51824753556<br>MASTER LICENCE: 3208417725,514</p>
  <footer class="site-footer">© 2013 Bracken Locksmiths. All Rights Reserved.</footer>
</main>
</body>
</html>
```